Trabworth Business Cards

We need a business card design for Trabworth Mining.

This is a B2B company that buys and sells large machinery tires within the coal mining industry. The design should the strong, crisp and masculine. I have uploaded the company logo and rough mock-up of what the back of the card should look like. the front of the card should have the same look/feel as the back. I need editable templates for both the front and the back of the card.

Color scheme should be grey/green/black

Contact information to include on the card:
Name: Dale Pembrose
Title: Managing Director
Phone: 555-314-2069
Address: 1187 Welford #3 Dallas, TX 75290
Email: Dale@Trabworth-example.com

I am also opening a contest for letterhead design. If you submit a business card design, please also submit a letterhead design with the same look/feel. The winner of the business card design will also will the letter head and be paid for both.

Target Market(s)

Procurement men/women in the coal mining industry

Industry/Entity Type

Coal Mining

```html
<!DOCTYPE html>
<html lang="en">
<head>
<meta charset="utf-8">
<title>Trabworth Mining Business Cards</title>
<link rel="stylesheet" href="https://fonts.googleapis.com/css2?family=Ubuntu:wght@400;500;700&display=swap">
<style>
  :root {
    --backdrop: #e4e4e2;
    --card-white: #ffffff;
    --card-dark: #2b2b2b;
    --ink: #2a2a2a;
    --ink-soft: #555657;
    --green: #5aa52c;
    --on-dark: #ffffff;
  }
  * { margin: 0; padding: 0; box-sizing: border-box; }
  html, body {
    width: 1200px; height: 900px; overflow: hidden;
    background: var(--backdrop);
    font-family: "Ubuntu", sans-serif;
  }
  .stage { position: relative; width: 1200px; height: 900px; }
  .card {
    position: absolute; left: 354px; width: 488px; height: 277px;
    box-shadow: 0 2px 6px rgba(0,0,0,0.18);
    overflow: hidden;
  }
  .card-front { top: 162px; background: var(--card-white); }
  .card-back { top: 472px; background: var(--card-dark); }

  .wordmark {
    position: absolute; display: flex; align-items: center; gap: 10px;
    font-family: "Ubuntu", sans-serif; font-weight: 500;
    font-size: 24px; letter-spacing: 1px; line-height: 1;
    white-space: nowrap;
  }
  .wordmark-square { width: 30px; height: 30px; background: var(--green); flex: none; }
  .card-front .wordmark { left: 24px; top: 53px; color: var(--ink-soft); }
  .card-back .wordmark { left: 0; right: 0; top: 117px; justify-content: center; color: var(--on-dark); }

  .holder { position: absolute; left: 23px; top: 199px; color: var(--ink); white-space: nowrap; }
  .holder-name { font-weight: 700; font-size: 15px; }
  .holder-title { font-size: 12px; margin-left: 3px; text-transform: uppercase; }

  .contact-line {
    position: absolute; left: 23px; right: 16px; top: 235px;
    font-size: 11.5px; color: var(--ink); white-space: nowrap;
  }
  .contact-line .sep { color: var(--green); margin: 0 3px; }

  .texture { position: absolute; inset: 0; background: linear-gradient(180deg, #303030 0%, #2a2a2a 60%, #282828 100%); }

  .web-rule { position: absolute; top: 188px; height: 2px; background: var(--green); }
  .web-rule.left { left: 0; width: 156px; }
  .web-rule.right { left: 333px; right: 0; }
  .web-address {
    position: absolute; left: 0; right: 0; top: 179px; text-align: center;
    font-size: 14px; letter-spacing: 0.5px; color: var(--green);
  }
</style>
</head>
<body>
<main class="stage">
  <section class="card card-front" aria-label="Business card front">
    <div class="wordmark"><span class="wordmark-square"></span>TRABWORTH MINING</div>
    <p class="holder"><span class="holder-name">Dale Pembrose</span><span class="holder-title">Managing Director</span></p>
    <p class="contact-line">555-314-2069<span class="sep">|</span>Dale@Trabworth-example.com<span class="sep">|</span>1187 Welford #3 Dallas, TX 75290</p>
  </section>

  <section class="card card-back" aria-label="Business card back">
    <div class="texture" role="img" aria-label="Subtle dark hexagon texture across the card"></div>
    <div class="wordmark"><span class="wordmark-square"></span>TRABWORTH MINING</div>
    <span class="web-rule left"></span>
    <p class="web-address">www.Trabworth.com</p>
    <span class="web-rule right"></span>
  </section>
</main>
</body>
</html>
```